Classy, Elegant, Simple Business Card Design

Looking to have a classy, simple, and elegant design. Want a top notch designed business card. I really like the look of the new torvane credit card. I also like the design I attached. I am trying to reach 21-29 year old females for booking us for there wedding or event. We offer Disc Jockey Service, Photo Booth Rentals, and Uplighting .

Target Market(s)

21-28 year old females

Contact Information for Business Card

Has to have logo, website, email, and phone number

Font styles to use
Other font styles liked:
• open to font choice, modern, clean
Designer to choose
33a6d7
0791cd
0555a3
ffffff

Requirements
Must have
• Has to have logo, website, email, and phone number
Nice to have
• I really like the design of the new torvane credit card. I also included my logo and some designs I like
Should not have
• clutter or too much info

```html
<!DOCTYPE html>
<html lang="en">
<head>
<meta charset="UTF-8">
<title>Harborlight Event Group – Business Card</title>
<link href="https://fonts.googleapis.com/css2?family=Montserrat:wght@400;500;600;700&display=swap" rel="stylesheet">
<style>
  :root {
    --backdrop: #c9cacc;
    --card: #f4f4f2;
    --brand-blue: #0791cd;
    --brand-sky: #33a6d7;
    --brand-navy: #0555a3;
    --ink-navy: #1c3a6b;
    --ink-grey: #8a8f96;
    --emboss: #e6e6e3;
    --card-shadow: rgba(0, 0, 0, 0.18);
  }
  * { margin: 0; padding: 0; box-sizing: border-box; }
  html, body {
    width: 1200px;
    height: 800px;
    overflow: hidden;
  }
  body {
    background: var(--backdrop);
    font-family: "Montserrat", Arial, sans-serif;
    display: flex;
    align-items: center;
    justify-content: center;
    gap: 60px;
  }
  .card {
    width: 525px;
    height: 300px;
    background: var(--card);
    box-shadow: 0 10px 28px var(--card-shadow);
    position: relative;
  }

  /* Front */
  .card-front {
    display: flex;
    align-items: center;
    padding: 0 34px 0 40px;
  }
  .brand {
    width: 230px;
    display: flex;
    align-items: center;
    gap: 10px;
  }
  .brand-dot {
    width: 22px;
    height: 22px;
    border-radius: 50%;
    background: var(--brand-blue);
    flex-shrink: 0;
  }
  .brand-name {
    font-weight: 600;
    font-size: 19px;
    line-height: 1.2;
    letter-spacing: 0.04em;
    color: var(--brand-blue);
    text-transform: uppercase;
  }
  .divider {
    width: 2px;
    height: 120px;
    background: var(--ink-navy);
    margin: 0 24px 0 14px;
    flex-shrink: 0;
  }
  .contact { color: var(--ink-navy); }
  .contact-name {
    font-size: 19px;
    font-weight: 500;
    letter-spacing: 0.02em;
    text-transform: uppercase;
  }
  .contact-name .surname {
    color: var(--brand-blue);
    font-weight: 700;
  }
  .contact-role {
    font-size: 13px;
    margin-bottom: 8px;
  }
  .contact-address {
    font-size: 12.5px;
    line-height: 1.35;
    margin-bottom: 4px;
  }
  .contact-list { list-style: none; }
  .contact-list li {
    display: flex;
    align-items: center;
    gap: 7px;
    font-size: 12.5px;
    line-height: 1.5;
  }
  .contact-icon {
    width: 10px;
    height: 10px;
    fill: var(--ink-navy);
    flex-shrink: 0;
  }

  /* Back */
  .card-back {
    display: flex;
    align-items: flex-end;
    justify-content: flex-end;
    padding: 0 40px 46px 0;
  }
  .back-mark {
    font-size: 30px;
    font-weight: 600;
    letter-spacing: 0.06em;
    color: var(--emboss);
    text-transform: uppercase;
  }
</style>
</head>
<body>
  <section class="card card-front" aria-label="Business card front">
    <div class="brand">
      <span class="brand-dot"></span>
      <span class="brand-name">Harborlight Event Group</span>
    </div>
    <div class="divider"></div>
    <div class="contact">
      <p class="contact-name">Mara <span class="surname">Ellison</span></p>
      <p class="contact-role">Manager</p>
      <p class="contact-address">48 Quay Street, Lakeport<br>ME 04011</p>
      <ul class="contact-list">
        <li>
          <svg class="contact-icon" viewBox="0 0 10 10" aria-hidden="true"><path d="M2 0.5 L3.6 0.5 L4.3 2.8 L3.2 3.6 Q4.2 5.8 6.4 6.8 L7.2 5.7 L9.5 6.4 L9.5 8 Q9.5 9.5 8 9.5 Q0.5 9 0.5 2 Q0.5 0.5 2 0.5 Z"/></svg>
          555-018-2100
        </li>
        <li>
          <svg class="contact-icon" viewBox="0 0 10 10" aria-hidden="true"><path d="M0.5 2 H9.5 V8.5 H0.5 Z M1 2.3 L5 5.4 L9 2.3" stroke="#f4f4f2" stroke-width="0.8"/></svg>
          hello@harborlight.com
        </li>
        <li>
          <svg class="contact-icon" viewBox="0 0 10 10" aria-hidden="true"><circle cx="5" cy="5" r="4.6"/><path d="M0.6 5 H9.4 M5 0.5 Q2.5 5 5 9.5 M5 0.5 Q7.5 5 5 9.5" stroke="#f4f4f2" stroke-width="0.7" fill="none"/></svg>
          www.harborlight.com
        </li>
      </ul>
    </div>
  </section>

  <section class="card card-back" aria-label="Business card back">
    <span class="back-mark">Harborlight</span>
  </section>
</body>
</html>
```